Copper Ridge Inquiries Letterhead

I would like to design a letterhead for a private investigation company. Our primary clients will be law firms. The business card is included below

```html
<!DOCTYPE html>
<html lang="en">
<head>
<meta charset="utf-8">
<title>Copper Ridge Inquiries Letterhead</title>
<link href="https://fonts.googleapis.com/css2?family=Montserrat:wght@800&family=Open+Sans:wght@400;600&display=swap" rel="stylesheet">
<style>
  :root{
    --navy:#17325f;
    --orange:#f05a2e;
    --peach:#fde9df;
    --mist:#dcdce6;
    --paper:#ffffff;
    --backdrop:#e4e4e4;
  }
  *{margin:0;padding:0;box-sizing:border-box}
  html,body{width:1200px;height:686px;overflow:hidden;background:var(--backdrop)}
  .canvas{position:relative;width:1200px;height:686px}
  .letterhead{
    position:absolute;left:365px;top:39px;width:470px;height:608px;
    background:var(--paper);overflow:hidden;
    box-shadow:0 2px 10px rgba(0,0,0,.12);
    font-family:"Open Sans",sans-serif;
  }
  .header-rule{position:absolute;left:0;right:0;top:96px;height:1.5px;background:var(--navy)}
  .header-accent{position:absolute;left:175px;width:150px;top:95px;height:3.5px;background:var(--orange)}
  .brand{
    position:absolute;left:175px;width:150px;top:70px;
    display:flex;align-items:center;justify-content:center;gap:6px;
  }
  .brand-dot{width:9px;height:9px;border-radius:50%;background:var(--orange);flex:none}
  .brand-name{
    font-family:"Montserrat",sans-serif;font-weight:800;font-size:11.5px;
    color:var(--navy);white-space:nowrap;letter-spacing:.2px;
  }
  .motif{
    position:absolute;left:0;bottom:14px;width:330px;height:260px;
    background:radial-gradient(ellipse at 35% 70%, var(--peach) 0%, rgba(253,233,223,.55) 45%, rgba(220,220,230,.35) 70%, rgba(255,255,255,0) 90%);
  }
  .contact{
    position:absolute;right:218px;bottom:34px;
    text-align:right;color:var(--navy);font-size:10.5px;line-height:16px;
  }
  .contact-line{display:flex;align-items:center;justify-content:flex-end;gap:5px;white-space:nowrap}
  .contact-line svg{width:9px;height:9px;flex:none}
  .license-no{color:var(--orange)}
  .tagline{color:var(--orange);font-size:10.5px;letter-spacing:.3px;margin-top:2px;white-space:nowrap}
  .footer-band{position:absolute;left:0;right:0;bottom:0;height:14px}
</style>
</head>
<body>
<div class="canvas">
  <div class="letterhead">
    <div class="brand">
      <span class="brand-dot"></span>
      <span class="brand-name">COPPER RIDGE INQUIRIES</span>
    </div>
    <div class="header-rule"></div>
    <div class="header-accent"></div>

    <div class="motif" role="img" aria-label="Faint decorative background motif in soft peach and grey"></div>

    <div class="contact">
      <div class="contact-line">
        <svg viewBox="0 0 10 10"><path d="M2 1 L4 1 L4.6 3.2 L3.4 4 Q4.4 6 6 6.6 L6.8 5.4 L9 6 L9 8 Q8 9.4 6 8.6 Q2 7 1 3.6 Q0.8 1.8 2 1Z" fill="var(--orange)"/></svg>
        <span>210.555.0142</span>
      </div>
      <div class="contact-line">
        <svg viewBox="0 0 10 10"><path d="M5 0.6 A3.4 3.4 0 0 1 8.4 4 C8.4 6.4 5 9.6 5 9.6 C5 9.6 1.6 6.4 1.6 4 A3.4 3.4 0 0 1 5 0.6Z M5 2.6 A1.4 1.4 0 1 0 5.01 2.6Z" fill="var(--orange)" fill-rule="evenodd"/></svg>
        <span>Marlow Springs, TX</span>
      </div>
      <div class="contact-line">
        <svg viewBox="0 0 10 10"><circle cx="5" cy="3.6" r="3" fill="var(--orange)"/><path d="M3.2 6 L2.4 9.6 L5 8.4 L7.6 9.6 L6.8 6Z" fill="var(--orange)"/></svg>
        <span>License NO. <span class="license-no">04729163</span></span>
      </div>
      <div class="contact-line">
        <svg viewBox="0 0 10 10"><rect x="0.6" y="2" width="8.8" height="6.2" fill="var(--orange)"/><path d="M0.8 2.3 L5 5.6 L9.2 2.3" fill="none" stroke="#fff" stroke-width="0.9"/></svg>
        <span>dana@copperridgeinquiries.com</span>
      </div>
      <div class="tagline">OVER 20 YEARS OF INVESTIGATIVE EXPERIENCE</div>
    </div>

    <svg class="footer-band" viewBox="0 0 470 14" preserveAspectRatio="none" aria-hidden="true">
      <rect x="0" y="0" width="200" height="14" fill="var(--orange)"/>
      <polygon points="200,0 212,0 226,14 214,14" fill="var(--navy)"/>
      <polygon points="216,0 228,0 242,14 230,14" fill="var(--orange)"/>
      <polygon points="232,0 470,0 470,14 246,14" fill="var(--navy)"/>
    </svg>
  </div>
</div>
</body>
</html>
```